Rehabilitation Centre Driving Evaluation brochure

I have already designed a brochure when I was at my previous workplace, but need a new one for my own rehab clinic. I will attach the brochure that I already did, as the information hasn't really changed. It is just very old and very ugly. It is an information pamphlet that will be in physician offices. Please let me know if you need anything else.

Target Market(s)

physicians, rehabilitation professionals, therapists, and individuals with medical conditions who want to return to driving

Industry/Entity Type

Medical

Requirements
Nice to have
• I am not stuck on the trifold, and actually may prefer a single fold brochure.

```html
<!DOCTYPE html>
<html lang="en">
<head>
<meta charset="utf-8">
<title>Driving Evaluation and Training Center Brochure</title>
<link rel="stylesheet" href="https://fonts.googleapis.com/css2?family=Questrial&family=Oswald:wght@600&display=swap">
<style>
  :root {
    --navy: #1e4a6d;
    --navy-dark: #163a57;
    --lime: #b3c300;
    --ink: #2a4a66;
    --paper: #ffffff;
    --backdrop: #d9d9d9;
  }
  * { margin: 0; padding: 0; box-sizing: border-box; }
  html, body { width: 960px; height: 1200px; overflow: hidden; }
  body {
    background: radial-gradient(ellipse at center, #f2f2f2 0%, var(--backdrop) 100%);
    font-family: "Questrial", "Century Gothic", sans-serif;
    color: var(--ink);
    position: relative;
  }
  .spread {
    position: absolute;
    left: 60px;
    width: 840px;
    height: 540px;
    display: flex;
    box-shadow: 0 10px 30px rgba(0,0,0,.18);
  }
  .spread--outer { top: 30px; }
  .spread--inner { top: 620px; }
  .page {
    position: relative;
    width: 420px;
    height: 540px;
    background: var(--paper);
    overflow: hidden;
  }
  .page + .page { border-left: 1px solid #e6e6e6; }
  .page svg.shapes { position: absolute; inset: 0; }
  .heading { color: var(--lime); font-size: 15px; margin-bottom: 5px; font-weight: 400; }
  .heading--navy { color: var(--navy); font-size: 15px; }
  .subhead { color: var(--lime); font-size: 10.5px; margin: 8px 0 3px; }
  .copy { font-size: 9px; line-height: 1.4; }
  .copy + .copy { margin-top: 6px; }
  .on-navy { color: #ffffff; }

  /* back cover */
  .referral { position: absolute; left: 30px; top: 36px; width: 330px; }
  .brand {
    display: flex; align-items: center; gap: 8px;
    color: var(--navy); font-size: 18px; line-height: 1.15;
  }
  .brand__dot { width: 14px; height: 14px; border-radius: 50%; background: var(--lime); flex: none; }
  .back-brand { position: absolute; left: 40px; top: 335px; width: 240px; }
  .contacts { position: absolute; left: 42px; top: 405px; list-style: none; font-size: 11px; color: var(--navy); }
  .contacts li { display: flex; align-items: flex-start; gap: 9px; margin-bottom: 6px; }
  .contacts svg { flex: none; margin-top: 1px; }

  /* front cover */
  .cover-title {
    position: absolute; right: 30px; top: 40px; width: 240px; text-align: right;
    font-family: "Oswald", "Arial Narrow", sans-serif; font-weight: 600;
    color: #fff; font-size: 24px; line-height: 1.05; letter-spacing: .5px;
  }
  .front-brand { position: absolute; left: 30px; top: 330px; width: 230px; }
  .tagline { position: absolute; left: 40px; top: 410px; font-size: 14px; color: var(--navy); line-height: 1.2; }
  .tagline span { display: block; color: var(--lime); padding-left: 26px; }
  .cover-web { position: absolute; left: 40px; top: 475px; font-size: 9px; color: #9aa5ae; }

  /* inner left */
  .assessment { position: absolute; left: 30px; top: 96px; width: 272px; }
  .assessment section { margin-bottom: 10px; }
  .assessment .copy { font-size: 8.6px; line-height: 1.36; }
  .assessment .copy + .copy { margin-top: 5px; }

  /* inner right */
  .programs { position: absolute; left: 30px; top: 30px; width: 340px; }
  .training { position: absolute; left: 30px; top: 360px; width: 200px; }
  .training .heading { color: var(--navy); font-size: 12px; }
</style>
</head>
<body>

<div class="spread spread--outer">
  <!-- back cover -->
  <article class="page page--back">
    <svg class="shapes" width="420" height="540" viewBox="0 0 420 540">
      <defs>
        <linearGradient id="navyGlow" x1="0" y1="0" x2="1" y2="1">
          <stop offset="0" stop-color="#1e4a6d"/><stop offset=".7" stop-color="#2f5b7e"/><stop offset="1" stop-color="#1a4262"/>
        </linearGradient>
      </defs>
      <path d="M0,0 H420 V150 C330,230 170,270 0,270 Z" fill="url(#navyGlow)"/>
    </svg>
    <div class="referral on-navy">
      <h2 class="heading">Referral Process</h2>
      <p class="copy">Referrals may be made by physicians, therapists, individuals requiring service, insurance companies, case managers, community service agencies, etc. The referral source will be asked to complete a referral form. The client's physician will be contacted and asked to complete a medical referral form stating the client is medically able to participate in the assessment.</p>
      <p class="copy">Referrals can be made for any individual who requires an evaluation of their driving skills or adaptive equipment needs by contacting us.</p>
    </div>
    <div class="brand back-brand"><span class="brand__dot"></span><span>Northway Rehabilitation Associates</span></div>
    <ul class="contacts">
      <li><svg width="11" height="13" viewBox="0 0 11 13"><path d="M5.5 0.5a4.5 4.5 0 0 0-4.5 4.5c0 3.3 4.5 7.5 4.5 7.5s4.5-4.2 4.5-7.5a4.5 4.5 0 0 0-4.5-4.5z" fill="none" stroke="#b3c300" stroke-width="1.3"/><circle cx="5.5" cy="5" r="1.6" fill="#b3c300"/></svg><span>2280 Cedarline Road, Unit 4<br>Riverton, Ontario, N0R 2K5</span></li>
      <li><svg width="11" height="11" viewBox="0 0 11 11"><path d="M2 0.5l2 2.2-1 1.3a7 7 0 0 0 4 4l1.3-1 2.2 2-1.2 1.5C4.8 10.5 0.5 6.2 0.5 1.7z" fill="#1e4a6d"/></svg><span>555 010 2480</span></li>
      <li><svg width="11" height="11" viewBox="0 0 11 11"><rect x="0.5" y="3.5" width="10" height="6" rx="1" fill="#b3c300"/><rect x="2.5" y="0.5" width="6" height="3.5" fill="#1e4a6d"/></svg><span>555 010 2481</span></li>
      <li><svg width="11" height="9" viewBox="0 0 11 9"><rect x="0.5" y="0.5" width="10" height="8" fill="none" stroke="#b3c300"/><path d="M0.5 0.5l5 4 5-4" fill="none" stroke="#b3c300"/></svg><span>office@northwayrehab.ca</span></li>
      <li><svg width="11" height="11" viewBox="0 0 11 11"><circle cx="5.5" cy="5.5" r="5" fill="none" stroke="#b3c300"/><path d="M0.5 5.5h10M5.5 0.5c-2.5 3-2.5 7 0 10M5.5 0.5c2.5 3 2.5 7 0 10" fill="none" stroke="#b3c300" stroke-width=".8"/></svg><span>www.northwayrehab.ca</span></li>
    </ul>
  </article>

  <!-- front cover -->
  <article class="page page--front">
    <svg class="shapes" width="420" height="540" viewBox="0 0 420 540">
      <defs>
        <linearGradient id="nightTraffic" x1="0" y1="0" x2="1" y2="1">
          <stop offset="0" stop-color="#8c9fb8"/><stop offset=".45" stop-color="#4d6b8f"/><stop offset="1" stop-color="#1d2c45"/>
        </linearGradient>
      </defs>
      <path d="M18,0 H420 V420 C340,370 260,320 215,250 C160,170 80,100 18,0 Z" fill="#1e4a6d"/>
      <path d="M6,0 C50,110 110,200 215,275" fill="none" stroke="#b3c300" stroke-width="9"/>
      <path d="M100,0 H420 V390 C340,340 270,300 235,230 C190,150 130,80 100,0 Z" fill="url(#nightTraffic)" role="img" aria-label="Photo of a car tail light in blurred evening traffic"/>
    </svg>
    <h1 class="cover-title">DRIVING EVALUATION AND TRAINING CENTER</h1>
    <div class="brand front-brand"><span class="brand__dot"></span><span>Northway Rehabilitation Associates</span></div>
    <p class="tagline">A comprehensive <span>driver rehabilitation program</span></p>
    <p class="cover-web">www.northwayrehab.ca</p>
  </article>
</div>

<div class="spread spread--inner">
  <!-- inner left -->
  <article class="page page--inside-left">
    <svg class="shapes" width="420" height="540" viewBox="0 0 420 540">
      <defs>
        <linearGradient id="foggyRoad" x1="0" y1="0" x2="0" y2="1">
          <stop offset="0" stop-color="#8f9396"/><stop offset=".6" stop-color="#c6c9cb"/><stop offset="1" stop-color="#ffffff" stop-opacity="0"/>
        </linearGradient>
      </defs>
      <path d="M335,0 H420 V260 C385,200 350,120 335,0 Z" fill="url(#foggyRoad)" role="img" aria-label="Faded photo of a car on a misty country road"/>
      <path d="M318,0 C330,130 365,210 420,270" fill="none" stroke="#b3c300" stroke-width="9"/>
    </svg>
    <div class="assessment">
      <section>
        <h2 class="heading heading--navy">Reason for Assessment</h2>
        <p class="copy">Each physician is required by law to report to the Ministry of Transportation any individual whose driving skills may be affected as a result of illness or injury. Therefore, the client's driver's licence may be placed under medical suspension. If this occurs, the client will be asked to undergo a driving evaluation from an Ontario Driver Assessment Centre.</p>
        <p class="copy">Individuals affected by illness, injury, or the aging process, whose driving skills have the potential to be affected, are also encouraged to undergo an evaluation of driving skills. The evaluation is designed to assess each client's ability to safely operate a motor vehicle and provide recommendations as needed.</p>
      </section>
      <section>
        <h2 class="heading heading--navy">Eligibility</h2>
        <p class="copy">Most individuals with disabilities are eligible for an evaluation of their ability to drive. Clients must have a valid driver's licence or the ability to obtain a temporary driver's licence or learner's permit.</p>
      </section>
      <section>
        <h2 class="heading heading--navy">What we do?</h2>
        <p class="copy">Our rehabilitation associates are committed to providing optimal rehabilitation service in a cost effective manner.</p>
        <p class="copy">We offer a multi-disciplinary, client-centred program of assessment, treatment and consultation for clients with physical, cognitive and/or perceptual impairments. We are aware each client is unique, therefore each program is tailored according to the individual's needs and personal goals.</p>
        <p class="copy">The driving assessment and training program is part of our comprehensive rehabilitation services. It is a service which represents our dedication to assist all individuals achieve optimal independence. Driving is an integral skill which is often essential for independence in the community.</p>
      </section>
    </div>
  </article>

  <!-- inner right -->
  <article class="page page--inside-right">
    <svg class="shapes" width="420" height="540" viewBox="0 0 420 540">
      <defs>
        <linearGradient id="navyPanel" x1="0" y1="0" x2="1" y2="1">
          <stop offset="0" stop-color="#1a4262"/><stop offset=".5" stop-color="#2d5a7d"/><stop offset="1" stop-color="#1e4a6d"/>
        </linearGradient>
        <linearGradient id="wheelPhoto" x1="0" y1="0" x2="1" y2="1">
          <stop offset="0" stop-color="#e9d9b8"/><stop offset=".5" stop-color="#6d6a66"/><stop offset="1" stop-color="#2a2a2c"/>
        </linearGradient>
      </defs>
      <path d="M0,0 H420 V470 C300,420 150,360 0,230 Z" fill="url(#navyPanel)"/>
      <circle cx="345" cy="390" r="66" fill="#ffffff"/>
      <circle cx="345" cy="390" r="60" fill="url(#wheelPhoto)" role="img" aria-label="Photo of a hand on a car steering wheel"/>
    </svg>
    <div class="programs on-navy">
      <h2 class="heading">Program Components &amp; Services</h2>
      <h3 class="subhead">Clinical Evaluation</h3>
      <p class="copy">The client is assessed by a certified occupational therapist. The client is initially seen in clinic for an assessment of physical, cognitive, and perceptual functioning as they relate to driving. The in-clinic portion of the assessment provides the therapist with information regarding medical history, driving history, knowledge of road signs and driving rules, physical abilities, cognitive status, visual and perceptual skills.</p>
      <h3 class="subhead">On the Road Evaluation</h3>
      <p class="copy">Following the in-clinic assessment, each client is then assessed in car by the therapist together with a certified driving instructor. The portion of the evaluation provides valuable information regarding the individual's functional driving skills.</p>
      <h3 class="subhead">Evaluation Equipment Needs</h3>
      <p class="copy">During the evaluation, it will be determined whether adaptive equipment will be necessary to improve the client's ability to drive safely. Recommendations will be made for adaptive equipment and installation.</p>
    </div>
    <div class="training">
      <h2 class="heading">Training &amp; Follow-up Services</h2>
      <p class="copy">Clients are commonly seen following a driving evaluation for training with driving skills or adaptive equipment. Further involvement with the occupational therapist may be indicated for cognitive or perceptual retraining, mobility-aid prescription, vehicle modification, or consultation with appropriate new vehicle purchase.</p>
    </div>
  </article>
</div>

</body>
</html>
```